ReelBloom business card

We are a performing arts company providing training (to both kids and adults) as well as performers for events. We hope to bring joy and confidence on stage to the people we train, as well as joy to the audience when our artistes perform. Designs should convey the joy, confidence and vibrancy on stage. Design business card using the attached logo. Card to include name, mobile tel, email address, company address, and website. Double sided. To also include the following list of what the company does:
• Training & Enrichment
• Private & Corporate Entertainment
- Music composition & production

Industry/Entity Type

Training

Contact Information for Business Card

Card to include name, mobile tel, email address, company address, and website. Double sided. To also include the following list of what the company does:
• Training & Enrichment

Requirements
Nice to have
• Card need not be the traditional rectangular in shape but not too outrageous.

```html
<!DOCTYPE html>
<html lang="en">
<head>
<meta charset="utf-8">
<title>ReelBloom business card</title>
<link rel="stylesheet" href="https://fonts.googleapis.com/css2?family=Arimo:wght@400;700&display=swap">
<style>
  :root {
    --backdrop: #3a3b3f;
    --paper: #fbfcfc;
    --ink: #2a2a2a;
    --pink: #e3195a;
    --violet: #8a5aa8;
    --blue: #1485d8;
    --white: #ffffff;
    --mic-grey: #d9dbdc;
  }
  * { box-sizing: border-box; margin: 0; padding: 0; }
  html, body { width: 1200px; height: 960px; overflow: hidden; }
  body {
    background: var(--backdrop);
    font-family: "Arimo", Arial, sans-serif;
    position: relative;
  }
  .card {
    position: absolute;
    left: 250px;
    width: 700px;
    height: 400px;
    border-radius: 26px;
    background: var(--paper);
    overflow: hidden;
    box-shadow: 0 10px 30px rgba(0,0,0,.35);
  }
  .card--services { top: 60px; }
  .card--contact { top: 500px; }

  /* services side */
  .brand-mark {
    position: absolute;
    top: 46px; right: 60px;
    display: flex; align-items: center; gap: 10px;
    font-weight: 700; font-size: 26px; color: var(--pink);
  }
  .brand-mark .dot {
    width: 14px; height: 14px; border-radius: 50%; background: var(--blue);
  }
  .service-list {
    position: absolute;
    top: 170px; left: 290px;
    list-style: none;
  }
  .service-list li {
    font-size: 25px; color: var(--ink);
    line-height: 40px;
    display: flex; align-items: center; gap: 14px;
  }
  .service-list li::before {
    content: ""; width: 15px; height: 15px;
    background: linear-gradient(135deg, var(--pink), var(--blue));
  }
  .mic-decor {
    position: absolute;
    left: 60px; bottom: -40px;
    width: 210px; height: 210px; border-radius: 50%;
    background: radial-gradient(circle, var(--mic-grey), rgba(217,219,220,0) 70%);
  }

  /* contact side */
  .brand-block {
    position: absolute;
    left: 0; top: 0; width: 300px; height: 100%;
    display: flex; align-items: center; justify-content: center;
  }
  .brand-name {
    display: flex; align-items: center; gap: 10px;
    font-weight: 700; font-size: 38px; color: var(--pink);
  }
  .brand-name .dot {
    width: 16px; height: 16px; border-radius: 50%; background: var(--blue);
  }
  .contact-panel {
    position: absolute;
    left: 300px; top: 0; right: 0; bottom: 40px;
    background: linear-gradient(160deg, var(--pink) 20%, var(--violet) 55%, var(--blue) 90%);
    padding: 70px 40px 0 44px;
    color: var(--white);
  }
  .contact-panel::after {
    content: ""; position: absolute; left: 0; right: 0; bottom: -40px; height: 40px;
    background: linear-gradient(90deg, var(--paper) 0, var(--paper) 0);
  }
  .person-name { font-size: 32px; font-weight: 700; margin-bottom: 30px; }
  .contact-list { list-style: none; }
  .contact-list li {
    display: flex; align-items: center; gap: 14px;
    font-size: 20px; line-height: 36px;
  }
  .contact-list svg { width: 24px; height: 24px; flex: none; }
</style>
</head>
<body>

<section class="card card--services" aria-label="Services side">
  <div class="brand-mark"><span class="dot"></span>ReelBloom</div>
  <ul class="service-list">
    <li>Training &amp; Enrichment</li>
    <li>Private &amp; Corporate Entertainment</li>
    <li>Music composition &amp; production</li>
  </ul>
  <div class="mic-decor" role="img" aria-label="Faint vintage microphone decoration"></div>
</section>

<section class="card card--contact" aria-label="Contact side">
  <div class="brand-block">
    <div class="brand-name"><span class="dot"></span>ReelBloom</div>
  </div>
  <div class="contact-panel">
    <h1 class="person-name">Your Name</h1>
    <ul class="contact-list">
      <li>
        <svg viewBox="0 0 24 24"><rect width="24" height="24" rx="4" fill="#fff"/><rect x="8" y="5" width="8" height="14" rx="1.5" fill="none" stroke="#333" stroke-width="2"/></svg>
        055-41260000
      </li>
      <li>
        <svg viewBox="0 0 24 24"><rect width="24" height="24" rx="4" fill="#fff"/><path d="M7 6c0 6 5 11 11 11l0-3-3-1-1.5 1.5c-2-1-3-2-4-4L11 9 10 6z" fill="#333"/></svg>
        776-52847700
      </li>
      <li>
        <svg viewBox="0 0 24 24"><rect width="24" height="24" rx="4" fill="#fff"/><rect x="5" y="7" width="14" height="10" fill="none" stroke="#333" stroke-width="2"/><path d="M5 7l7 6 7-6" fill="none" stroke="#333" stroke-width="2"/></svg>
        reelbloom@email.com
      </li>
      <li>
        <svg viewBox="0 0 24 24"><rect width="24" height="24" rx="4" fill="#fff"/><circle cx="12" cy="12" r="6" fill="none" stroke="#333" stroke-width="2"/><path d="M6 12h12M12 6v12" stroke="#333" stroke-width="1.5"/></svg>
        www.reelbloom.com
      </li>
      <li>
        <svg viewBox="0 0 24 24"><rect width="24" height="24" rx="4" fill="#fff"/><path d="M12 19s-5-5-5-9a5 5 0 0110 0c0 4-5 9-5 9z" fill="#333"/><circle cx="12" cy="10" r="2" fill="#fff"/></svg>
        4120, elm grove street MI 3300 US
      </li>
    </ul>
  </div>
</section>

</body>
</html>
```